Modern Business Card For A Digital Advertising Company

I'll be print on the Pell Prints Velour paper http://us.pellprints.com/products/velour/business-cards.html
Need's to be modern and use the color palette of the logo or gray scales. I think integrating the pixelation of the logo in to the card and having it wrap from one side to the other could be interesting. My company provides ad operations, web development, and number of other services to websites around the world. You can see my website at http://www.zantorhq.com
Contact info on the card needs to have
Owen Lasko
President
p.318.204.6637
owen@zantorhq.com
http://www.zantorhq.com
Doesn't necessarily need to be in that order
Website owners
Business

```html
<!DOCTYPE html>
<html lang="en">
<head>
<meta charset="utf-8">
<title>Zantor HQ Business Card</title>
<link href="https://fonts.googleapis.com/css2?family=Source+Sans+3:wght@400;600;700&display=swap" rel="stylesheet">
<style>
  :root {
    --backdrop: #4a2417;
    --card: #ffffff;
    --green: #8cc63f;
    --charcoal: #262626;
    --ink: #3a3a3a;
    --muted: #555555;
  }
  * { margin: 0; padding: 0; box-sizing: border-box; }
  html, body { width: 1200px; height: 448px; overflow: hidden; }
  body {
    background: var(--backdrop);
    font-family: "Source Sans 3", "Helvetica Neue", Arial, sans-serif;
    position: relative;
  }
  .card {
    position: absolute;
    background: var(--card);
    border-radius: 18px;
    overflow: hidden;
    box-shadow: 0 4px 12px rgba(0,0,0,0.35);
  }
  .card-front { left: 72px; top: 64px; width: 510px; height: 290px; }
  .card-back { left: 616px; top: 73px; width: 508px; height: 289px; }

  .brand {
    display: flex;
    align-items: center;
    gap: 10px;
    color: var(--green);
    font-weight: 700;
    letter-spacing: 1px;
  }
  .brand-mark { background: var(--green); flex: none; }

  .card-front .brand {
    position: absolute; left: 53px; top: 118px;
    font-size: 34px; line-height: 1;
  }
  .card-front .brand-mark { width: 26px; height: 26px; }

  .contact {
    position: absolute; left: 280px; top: 143px;
    list-style: none;
    font-size: 13px; line-height: 20px;
    color: var(--ink);
  }
  .contact-label { color: var(--green); margin-right: 4px; }

  .swoosh { position: absolute; left: 0; top: 0; width: 510px; height: 290px; }
  .swoosh-dark { fill: var(--charcoal); }
  .swoosh-green { fill: var(--green); }

  .person {
    position: absolute; left: 215px; top: 250px;
    display: flex; align-items: baseline; gap: 10px;
    color: var(--charcoal);
  }
  .person-name { font-size: 20px; font-weight: 700; }
  .person-divider { font-size: 18px; }
  .person-title { font-size: 12px; font-weight: 600; }

  .card-back .brand {
    position: absolute; left: 0; right: 0; top: 110px;
    justify-content: center;
    font-size: 44px; line-height: 1;
  }
  .card-back .brand-mark { width: 34px; height: 34px; }
  .back-url {
    position: absolute; left: 0; right: 0; top: 202px;
    text-align: center;
    font-size: 12px; letter-spacing: 2.6px;
    color: var(--muted);
  }
</style>
</head>
<body>
  <section class="card card-front">
    <div class="brand"><span class="brand-mark"></span><span class="brand-name">ZANTOR HQ</span></div>

    <ul class="contact">
      <li><span class="contact-label">T.</span> 318.204.6637</li>
      <li><span class="contact-label">E.</span> owen@zantorhq.com</li>
      <li><span class="contact-label">W.</span> http://www.zantorhq.com</li>
    </ul>

    <svg class="swoosh" viewBox="0 0 510 290" aria-hidden="true">
      <path class="swoosh-dark" d="M0,248 Q130,230 262,227 Q130,242 12,290 L0,290 Z"/>
      <path class="swoosh-green" d="M12,290 Q140,240 262,227 Q430,220 510,262 L510,290 Z"/>
    </svg>

    <div class="person">
      <span class="person-name">Owen Lasko</span>
      <span class="person-divider">|</span>
      <span class="person-title">President</span>
    </div>
  </section>

  <section class="card card-back">
    <div class="brand"><span class="brand-mark"></span><span class="brand-name">ZANTOR HQ</span></div>
    <p class="back-url">www.zantorhq.com</p>
  </section>
</body>
</html>
```